Business Cards for a law firm

Business cards for our law firm. Use our silhoette logo and OAK PARTNERS - check our website (www.oakpartners.example)

Contact Information for Business Card

our silhouette logo, OAK PARTNERS, 800-555-0147, Dorian Pemberton, dorian@oakpartners.example

Requirements
Must have
• our silhouette logo, OAK PARTNERS, 800-555-0147, Dorian Pemberton, dorian@oakpartners.example

```html
<!DOCTYPE html>
<html lang="en">
<head>
<meta charset="utf-8">
<title>Oak Partners — Business Cards</title>
<link href="https://fonts.googleapis.com/css2?family=Montserrat:wght@500;600;700&family=Open+Sans:wght@400&display=swap" rel="stylesheet">
<style>
  :root {
    --navy: #2a3a78;
    --navy-deep: #1f2c66;
    --blue-mid: #3d4f9a;
    --blue-light: #6677b8;
    --paper: #ffffff;
    --ink-soft: #555a6e;
    --rule: #8a93b8;
    --backdrop: #ecebe8;
  }
  * { margin: 0; padding: 0; box-sizing: border-box; }
  html, body { width: 1200px; height: 913px; overflow: hidden; }
  body {
    background: var(--backdrop);
    position: relative;
    font-family: "Open Sans", Arial, sans-serif;
  }
  .card {
    position: absolute;
    top: 308px;
    width: 520px;
    height: 297px;
    box-shadow: 0 6px 18px rgba(0,0,0,0.18);
    overflow: hidden;
  }
  /* Front */
  .card-front { left: 50px; background: var(--navy); }
  .card-front .pattern-area {
    position: absolute; inset: 0;
    background: linear-gradient(120deg, var(--navy-deep) 0%, var(--blue-mid) 40%, var(--blue-light) 55%, var(--blue-mid) 70%, var(--navy) 100%);
  }
  .card-front .brand {
    position: absolute;
    left: 150px; top: 132px;
    display: flex; align-items: center; gap: 12px;
  }
  .card-front .brand-dot {
    width: 26px; height: 26px; border-radius: 50%;
    background: var(--paper);
  }
  .card-front .brand-name {
    font-family: "Montserrat", Arial, sans-serif;
    font-weight: 600;
    font-size: 24px;
    letter-spacing: 2px;
    color: var(--paper);
  }
  /* Back */
  .card-back { left: 630px; background: var(--paper); }
  .card-back .brand-dot {
    position: absolute;
    left: 44px; top: 118px;
    width: 72px; height: 72px; border-radius: 50%;
    background: var(--navy);
  }
  .card-back .brand-name {
    position: absolute;
    left: 134px; top: 70px;
    font-family: "Montserrat", Arial, sans-serif;
    font-weight: 700;
    font-size: 36px;
    letter-spacing: 3px;
    color: var(--navy);
  }
  .card-back .person {
    position: absolute;
    left: 100px; top: 200px;
    width: 190px;
    text-align: right;
  }
  .card-back .person-name {
    font-family: "Montserrat", Arial, sans-serif;
    font-weight: 700;
    font-size: 18px;
    color: var(--navy);
  }
  .card-back .person-role {
    font-size: 12px;
    color: var(--ink-soft);
    margin-top: 1px;
  }
  .card-back .divider {
    position: absolute;
    left: 302px; top: 142px;
    width: 1px; height: 92px;
    background: var(--rule);
  }
  .card-back .contacts {
    position: absolute;
    left: 314px; top: 144px;
    list-style: none;
    font-size: 12px;
    color: var(--ink-soft);
  }
  .card-back .contacts li {
    display: flex; align-items: center; gap: 6px;
    height: 21px;
  }
  .card-back .contacts svg { width: 11px; height: 11px; flex: none; fill: var(--navy); }
</style>
</head>
<body>

  <section class="card card-front">
    <div class="pattern-area" role="img" aria-label="Repeating pattern of brand silhouettes on a glossy blue background"></div>
    <div class="brand">
      <span class="brand-dot"></span>
      <span class="brand-name">OAK PARTNERS</span>
    </div>
  </section>

  <section class="card card-back">
    <span class="brand-dot"></span>
    <span class="brand-name">OAK PARTNERS</span>

    <div class="person">
      <div class="person-name">Dorian Pemberton</div>
      <div class="person-role">Lawyer</div>
    </div>

    <div class="divider"></div>

    <ul class="contacts">
      <li>
        <svg viewBox="0 0 16 16" aria-hidden="true"><path d="M3.6 1.2l2.3 2.4-1.3 1.9c.9 2 2.5 3.6 4.5 4.5l1.9-1.3 2.4 2.3-1.5 2.6C7.2 13.4 2.6 8.8 1 3.1z"/></svg>
        800-555-0147
      </li>
      <li>
        <svg viewBox="0 0 16 16" aria-hidden="true"><path d="M1 3h14v10H1z M1.5 3.5L8 9l6.5-5.5" stroke="#fff" stroke-width="1.2"/></svg>
        dorian@oakpartners.example
      </li>
      <li>
        <svg viewBox="0 0 16 16" aria-hidden="true"><circle cx="8" cy="8" r="7"/><path d="M1 8h14M8 1c-3 3.5-3 10.5 0 14M8 1c3 3.5 3 10.5 0 14" stroke="#fff" stroke-width="1" fill="none"/></svg>
        www.oakpartners.example
      </li>
    </ul>
  </section>

</body>
</html>
```